Boutique Shoe Bag Race wear Business Card Design

We are a new luxury shoe bag, jewellery and race wear store stocking local and international designers. Located in the fashion precinct of beautiful Marlow Beach famous in Sydney Australia. Stocking French jewellery and shoes such as Henri Delacrouxs plus Australian made. Looking at quality and service and looking after the locals and tourists.
Ideas: White background, Black writing in bold engravers, logo in middle of Marlow and Boutique a gold horseshoe (facing upright so the curve is at the bottom) with a black stiletto inside. French clover silver and black border (not irish clover the French lattice type look)
Updates

Marlow Atelier

I open 8/4 so require business card design ASAP.

Please place gold horseshoe facing upwards with the black stiletto inside.

Bold engravers writing for business name.

I will have my phone number tomorrow to update.

Border in similar/same style as attached picture with black/silver clover French design.

Thank you. Nina                                   

Industry/Entity Type

Fashion

Contact Information for Business Card

Marlow Atelier
Boutique Owner Nina Pellard
41B Tilbury Lane
Marlow Beach NSW 2091 Australia
0471392605
02 **** *TBA
info@marlowatelier.com.au
Facebook.com/MarlowAtelier
www.marlowatelier.com.au

Font styles to use
Other font styles liked:
• Bold Engravers

Requirements
Must have
• Info on one side including business name and logo with black stiletto and gold horse shoe. reverse side with French clover border and Larger name Marlow Atelier with logo in centre.
Should not have
• irish clover
French script
horseshoe upside down

```html
<!DOCTYPE html>
<html lang="en">
<head>
<meta charset="utf-8">
<title>Marlow Atelier Business Card</title>
<link href="https://fonts.googleapis.com/css2?family=Cinzel:wght@400;600;700&family=Marcellus&display=swap" rel="stylesheet">
<style>
  :root {
    --backdrop: #e9e9e9;
    --card: #ffffff;
    --lattice: #8f8f8f;
    --ink: #111111;
    --ink-soft: #666666;
    --gold: #d8a930;
    --shadow: rgba(0,0,0,0.28);
  }
  html, body {
    margin: 0;
    width: 1200px;
    height: 1000px;
    overflow: hidden;
    background: var(--backdrop);
  }
  .canvas { position: relative; width: 1200px; height: 1000px; }
  .card {
    position: absolute;
    box-shadow: 8px 8px 14px var(--shadow);
    overflow: hidden;
  }
  .card--front { left: 334px; top: 130px; width: 554px; height: 342px; }
  .card--back { left: 334px; top: 510px; width: 556px; height: 344px; background: var(--card); }
  .card__svg { position: absolute; inset: 0; }
  .front-name {
    position: absolute;
    left: 0; width: 554px;
    top: 112px;
    text-align: center;
    font-family: "Cinzel", serif;
    font-weight: 600;
    font-size: 35px;
    line-height: 38px;
    color: var(--ink-soft);
  }
  .back-brand {
    position: absolute;
    left: 0; width: 556px;
    top: 88px;
    display: flex;
    justify-content: center;
    align-items: center;
    gap: 14px;
    font-family: "Cinzel", serif;
    font-weight: 700;
    font-size: 22px;
    letter-spacing: 4px;
    color: var(--ink);
  }
  .brand-dot {
    width: 34px; height: 34px;
    border-radius: 50%;
    background: var(--gold);
  }
  .owner {
    position: absolute;
    left: 115px; top: 160px;
    font-family: "Marcellus", serif;
    font-size: 14px;
    line-height: 18px;
    letter-spacing: 0.5px;
  }
  .owner__role { color: var(--ink-soft); }
  .owner__name { color: var(--ink); }
  .contacts {
    position: absolute;
    left: 270px; top: 158px;
    font-family: "Marcellus", serif;
    font-size: 13.5px;
    line-height: 19px;
    color: var(--ink-soft);
  }
  .address {
    position: absolute;
    left: 0; width: 556px;
    top: 246px;
    text-align: center;
    font-family: "Marcellus", serif;
    font-size: 14.5px;
    line-height: 19px;
    color: var(--ink);
  }
</style>
</head>
<body>
<div class="canvas">
  <section class="card card--front">
    <svg class="card__svg" width="554" height="342" viewBox="0 0 554 342">
      <rect class="lattice-fill" width="554" height="342" fill="var(--lattice)" role="img" aria-label="French quatrefoil lattice pattern in black and silver"/>
      <polygon class="hex-panel" points="131,110 275,48 426,110 426,242 275,306 131,242" fill="var(--card)"/>
      <circle cx="275" cy="232" r="30" fill="var(--gold)"/>
    </svg>
    <div class="front-name">MARLOW<br>ATELIER</div>
  </section>

  <section class="card card--back">
    <div class="back-brand">
      <span>MARLOW</span>
      <span class="brand-dot"></span>
      <span>ATELIER</span>
    </div>
    <div class="owner">
      <div class="owner__role">Boutique Owner</div>
      <div class="owner__name">Nina Pellard</div>
    </div>
    <div class="contacts">
      <div>02 **** *TBA</div>
      <div>info@marlowatelier.com.au</div>
      <div>Facebook.com/MarlowAtelier</div>
      <div>www.marlowatelier.com.au</div>
    </div>
    <div class="address">
      41B Tilbury Lane Marlow Beach NSW 2091<br>
      Australia 0471392605
    </div>
  </section>
</div>
</body>
</html>
```